Business card for law firm

Need business card for new law firm. Think confident, authoritative, conservative, but not stuffy or old-fashioned.

Contact Information for Business Card

Content for card - logo (uploaded), plus the following:

Paul Whitcombe (larger font)
Managing Partner (larger font, but not as large as name)
Level 9, 7 Ferris Lane
Sydney NSW 2000
Main Tel 02 9364 2710
Direct Tel 02 8472 3159
Email paul@qvlegal.com.au
www.qvlegal.com.au

Letterhead design should include logo plus:
Level 9, 7 Ferris Lane
Sydney NSW 2000
Tel 02 8472 3159
www.qvlegal.com.au

```html
<!DOCTYPE html>
<html lang="en">
<head>
<meta charset="utf-8">
<title>Quayvale Legal — Business Card</title>
<link rel="stylesheet" href="https://fonts.googleapis.com/css2?family=Cinzel:wght@500&family=Open+Sans:wght@400&display=swap">
<style>
  :root {
    --backdrop: #2b2b2d;
    --card: #ffffff;
    --navy: #0f1f5c;
    --ink: #1c1c1c;
    --rule: #c9c9c9;
  }
  * { box-sizing: border-box; margin: 0; padding: 0; }
  html, body {
    width: 1200px; height: 900px; overflow: hidden;
    background: var(--backdrop);
  }
  .sheet {
    width: 1200px; height: 900px;
    display: flex; flex-direction: column; align-items: center; justify-content: center;
    gap: 50px;
  }
  .card {
    position: relative;
    width: 630px; height: 360px;
    background: var(--card);
    border-bottom: 8px solid var(--navy);
  }
  /* Front */
  .card--front {
    display: flex; flex-direction: column; align-items: center; justify-content: center;
    gap: 26px;
  }
  .brand-mark {
    width: 58px; height: 58px; background: var(--navy);
  }
  .brand-name {
    font-family: "Cinzel", serif;
    font-weight: 500;
    font-size: 44px;
    letter-spacing: 0.06em;
    color: var(--navy);
  }
  /* Back */
  .card--back {
    padding: 0 40px;
  }
  .identity {
    position: absolute; left: 60px; top: 128px; width: 230px;
    text-align: right;
  }
  .identity__name {
    font-family: "Cinzel", serif; font-weight: 500;
    font-size: 25px; color: var(--navy); letter-spacing: 0.02em;
    white-space: nowrap;
  }
  .identity__role {
    font-family: "Open Sans", sans-serif;
    font-size: 17px; color: var(--ink); margin-top: 2px;
  }
  .divider {
    position: absolute; left: 318px; top: 118px;
    width: 1px; height: 84px; background: var(--rule);
  }
  .contacts {
    position: absolute; left: 340px; top: 116px;
    list-style: none;
    font-family: "Open Sans", sans-serif; font-size: 17px; color: var(--ink);
    line-height: 22px;
  }
  .contacts li { display: flex; align-items: center; gap: 7px; white-space: nowrap; }
  .contacts svg { width: 14px; height: 14px; fill: var(--navy); flex: none; }
  .contacts .note { font-size: 14px; }
  .address {
    position: absolute; left: 0; right: 0; top: 250px;
    text-align: center;
    font-family: "Open Sans", sans-serif; font-size: 17px; color: var(--ink);
  }
</style>
</head>
<body>
<main class="sheet">
  <section class="card card--front">
    <div class="brand-mark"></div>
    <div class="brand-name">Quayvale Legal</div>
  </section>

  <section class="card card--back">
    <div class="identity">
      <div class="identity__name">PAUL WHITCOMBE</div>
      <div class="identity__role">Managing Partner</div>
    </div>
    <div class="divider"></div>
    <ul class="contacts">
      <li>
        <svg viewBox="0 0 16 16" aria-hidden="true"><path d="M1 5c0-2 3-3 7-3s7 1 7 3v1h-4V5H5v1H1z M4 7h8l2 7H2z"/></svg>
        02 9364 2710
      </li>
      <li>
        <svg viewBox="0 0 16 16" aria-hidden="true"><path d="M1 5c0-2 3-3 7-3s7 1 7 3v1h-4V5H5v1H1z M4 7h8l2 7H2z"/></svg>
        02 8472 3159 <span class="note">(DIRECT)</span>
      </li>
      <li>
        <svg viewBox="0 0 16 16" aria-hidden="true"><path d="M1 3h14v10H1z M2 4l6 5 6-5z" fill-rule="evenodd"/></svg>
        paul@qvlegal.com.au
      </li>
      <li>
        <svg viewBox="0 0 16 16" aria-hidden="true"><circle cx="8" cy="8" r="7"/></svg>
        www.qvlegal.com.au
      </li>
    </ul>
    <p class="address">Level 9, 7 Ferris Lane Sydney NSW 2000</p>
  </section>
</main>
</body>
</html>
```